Vantrel System Web Page Design

This project is to design 6 pages of a web based medical system for clinics, hospitals, drugs suppliers, general items suppliers, insurance company, laboratories and patients (basically all parties which could be involved in).We want the designs of the browser, button, icon and layout are based on Zeltor, which is user friendly, looks professional, simple and neat but with powerful functions. We have uploaded few pictures of another system, please do not copy its design because this is not what we are looking for, the pictures are for you to know the elements should be included in our pages. Vantrel web-base system, design 6 pages1. Login PageShould include the following elements-company id with input field-login id with input field-password with input field2. Main Page (Navigation page)Should include the following elements-Appointment-Consultation-Patient-Drugs inventory -General supplies inventory -Laboratory-Suppliers-Insurance-Reports 3. Appointment PageShould include all the the elements in the respective pictures plus the followings-Daily View, Weekly View, Monthly View buttons4. Consultation PageShould include all the the elements in the respective picture5. Patient Page5.1 General information Should include all the the elements in the respective picture5.2 medical history/lab reportsShould include all the the elements in the respective picture plus the followings-Notify patient button-Share report button.
Updated on 28 Nov:
Please stop using Harbor Suite in your designs which is not the name of our system. We have just rename our system to Vantrel, please take note.
We need the system to look professional not playful, do not use too many colors and playful icons.

```html
<!DOCTYPE html>
<html lang="en">
<head>
<meta charset="utf-8">
<title>Vantrel – Screens</title>
<link href="https://fonts.googleapis.com/css2?family=Roboto:wght@400;500;700&display=swap" rel="stylesheet">
<style>
:root{
  --bg:#7cc3de;
  --navy:#1d3593;
  --royal:#2a2fc4;
  --red:#c8102e;
  --grey-bg:#e8e9ec;
  --footer:#d9d9db;
  --ink:#2b2b2b;
  --muted:#555;
  --dark-btn:#4a4d52;
  --white:#fff;
}
*{box-sizing:border-box;margin:0;padding:0}
html,body{width:1200px;height:2323px;overflow:hidden}
body{background:var(--bg);font-family:'Roboto',sans-serif;color:var(--ink);position:relative}
.screen{position:absolute;left:127px;width:944px;overflow:hidden}
/* login */
.login-screen{top:98px;height:506px;background:linear-gradient(135deg,#0f2236 0%,#1a3348 40%,#0c1a28 70%,#13273a 100%)}
.login-card{position:absolute;left:141px;top:85px;width:664px;height:291px;display:flex}
.login-brand{width:365px;background:var(--white);display:flex;flex-direction:column;align-items:center;justify-content:center}
.brand-name{font-weight:700;font-size:40px;color:var(--navy);letter-spacing:-.5px}
.brand-tag{font-size:14px;color:var(--navy);margin-top:4px;align-self:flex-end;margin-right:46px}
.login-form{flex:1;background:radial-gradient(circle at 70% 60%,#3b42e0 0%,var(--royal) 45%,#1a1f9c 100%);display:flex;flex-direction:column;align-items:center;padding-top:22px}
.login-form h1{color:var(--white);font-size:33px;font-weight:500;margin-bottom:16px}
.field{width:215px;height:34px;border-radius:17px;background:var(--white);font-size:10px;color:#555;padding:11px 14px;margin-bottom:9px}
.login-btn{margin-top:6px;width:116px;height:26px;border-radius:13px;background:var(--red);color:var(--white);font-size:13px;font-weight:700;display:flex;align-items:center;justify-content:center}
.forgot{color:var(--white);font-size:10px;margin-top:10px}
.login-copy{position:absolute;width:100%;top:452px;text-align:center;color:var(--white);font-size:13px}
/* app screens */
.app{background:var(--grey-bg)}
.app-header{position:absolute;top:0;left:0;width:100%;height:68px;background:var(--white);box-shadow:0 2px 6px rgba(0,0,0,.12)}
.app-header .logo{position:absolute;left:58px;top:13px;display:flex;flex-direction:column;align-items:flex-end;color:var(--navy)}
.app-header .logo-name{font-weight:700;font-size:26px;line-height:30px}
.app-header .logo-tag{font-size:8px;line-height:10px}
.app-header .phone{position:absolute;left:282px;top:25px;display:flex;align-items:center;gap:6px;font-size:13px}
.app-header .lang{position:absolute;left:427px;top:25px;font-size:13px}
.app-header .user{position:absolute;left:795px;top:17px;display:flex;align-items:center;gap:8px;font-size:11px;color:var(--muted)}
.avatar{width:34px;height:34px;border-radius:50%;background:linear-gradient(#9aa6b2,#4f5d6b)}
.app-footer{position:absolute;left:0;bottom:0;width:100%;height:65px;background:var(--footer);display:flex;align-items:center;justify-content:center;font-size:13px}
/* nav */
.nav-screen{top:677px;height:657px}
.module{position:absolute;width:152px;height:152px;border-radius:50%;background:var(--white);box-shadow:0 3px 10px rgba(0,0,0,.18);display:flex;flex-direction:column;align-items:center;justify-content:center;text-align:center;font-size:14px;gap:8px;transform:translate(-50%,-50%)}
.module svg{width:46px;height:46px}
.module.active{background:var(--red);color:var(--white)}
/* files */
.files-screen{top:1404px;height:814px}
.section-title{position:absolute;left:58px;top:92px;font-size:23px;font-weight:500}
.tile{position:absolute;width:156px;height:179px;background:var(--white);box-shadow:0 1px 3px rgba(0,0,0,.2)}
.thumb{height:131px;background:#000;display:flex;align-items:center;justify-content:center}
.scan{background:radial-gradient(circle at 55% 45%,#8aa0c8 0%,#3b4c70 35%,#05070d 75%)}
.ecg{background:linear-gradient(135deg,#3a1050,#12061e 60%,#1e0a2c)}
.tile-name{font-size:11px;color:var(--red);padding:6px 12px 0}
.tile-meta{display:flex;justify-content:space-between;align-items:center;font-size:10px;font-weight:700;padding:6px 12px}
.check{width:11px;height:11px;border:1px solid #666}
.btn{position:absolute;height:39px;display:flex;align-items:center;justify-content:center;font-size:15px;font-weight:500;color:var(--white);border-radius:2px}
.btn.blue{background:var(--navy)}
.btn.dark{background:var(--dark-btn);font-size:13px}
.btn.red{background:var(--red)}
.btn.outline-blue{background:var(--white);color:var(--navy);border:1px solid var(--navy)}
.btn.outline-red{background:var(--white);color:var(--red);border:1px solid var(--red)}
.divider{position:absolute;left:58px;top:664px;width:837px;height:2px;background:#bbb}
</style>
</head>
<body>

<section class="screen login-screen" role="img" aria-label="Dark blue faceted background">
  <div class="login-card">
    <div class="login-brand">
      <div class="brand-name">Vantrel</div>
      <div class="brand-tag">Professional Edition</div>
    </div>
    <form class="login-form">
      <h1>LOGIN</h1>
      <div class="field">Company Id</div>
      <div class="field">User Name</div>
      <div class="field">Password</div>
      <div class="login-btn">LOGIN</div>
      <div class="forgot">Forgot Password ?</div>
    </form>
  </div>
  <p class="login-copy">©Copyright 2018. All Rights Reserved.</p>
</section>

<section class="screen app nav-screen">
  <header class="app-header">
    <div class="logo"><span class="logo-name">Vantrel</span><span class="logo-tag">Professional Edition</span></div>
    <div class="phone"><svg width="18" height="18" viewBox="0 0 24 24"><circle cx="12" cy="12" r="10" fill="none" stroke="#c8102e" stroke-width="2"/><path d="M8 7l2 0 1 3-1.5 1a6 6 0 0 0 3.5 3.5l1-1.5 3 1v2a1 1 0 0 1-1 1A9 9 0 0 1 7 8a1 1 0 0 1 1-1z" fill="#c8102e"/></svg>(852) 3940 6127</div>
    <div class="lang">English ▾</div>
    <div class="user"><div class="avatar" role="img" aria-label="User avatar"></div>Ardenne ▾</div>
  </header>

  <div class="module" style="left:133px;top:238px"><svg viewBox="0 0 48 48"><rect x="4" y="8" width="40" height="26" rx="2" fill="#c8102e"/><rect x="8" y="12" width="32" height="18" fill="#fff"/><rect x="20" y="34" width="8" height="6" fill="#c8102e"/><rect x="14" y="40" width="20" height="3" fill="#c8102e"/></svg>Appointment</div>
  <div class="module" style="left:306px;top:238px"><svg viewBox="0 0 48 48" fill="#c8102e"><circle cx="24" cy="10" r="6"/><circle cx="10" cy="36" r="6"/><circle cx="38" cy="36" r="6"/><path d="M16 24l4-6M32 24l-4-6M18 40h12" stroke="#c8102e" stroke-width="3"/></svg>Consultation</div>
  <div class="module active" style="left:477px;top:238px"><svg viewBox="0 0 48 48"><rect x="8" y="6" width="32" height="38" rx="3" fill="none" stroke="#fff" stroke-width="3"/><path d="M24 14v12M18 20h12" stroke="#fff" stroke-width="3"/><path d="M14 34h20M14 39h14" stroke="#fff" stroke-width="2"/></svg>Patient</div>
  <div class="module" style="left:649px;top:238px"><svg viewBox="0 0 48 48" fill="#c8102e"><rect x="10" y="4" width="28" height="6"/><rect x="12" y="12" width="24" height="32" rx="2"/><path d="M24 20v14M17 27h14" stroke="#fff" stroke-width="4"/></svg>Drugs inventory</div>
  <div class="module" style="left:820px;top:238px"><svg viewBox="0 0 48 48" fill="#c8102e"><rect x="18" y="4" width="12" height="4"/><path d="M20 8h8v12l12 20a3 3 0 0 1-3 4H11a3 3 0 0 1-3-4l12-20z"/></svg>Laboratory</div>

  <div class="module" style="left:220px;top:434px"><svg viewBox="0 0 48 48" fill="#c8102e"><rect x="6" y="20" width="16" height="16"/><rect x="24" y="14" width="18" height="22"/><rect x="4" y="38" width="40" height="3"/><circle cx="12" cy="44" r="3"/><circle cx="36" cy="44" r="3"/></svg>Suppliers</div>
  <div class="module" style="left:395px;top:434px"><svg viewBox="0 0 48 48"><path d="M8 6h32v18c0 10-8 16-16 20C16 40 8 34 8 24z" fill="#c8102e"/><path d="M16 12h10v20c-6-3-10-7-10-12z" fill="#fff"/></svg>General supplies<br>inventory</div>
  <div class="module" style="left:563px;top:434px"><svg viewBox="0 0 48 48"><path d="M12 4h18l10 10v30H12z" fill="#c8102e"/><path d="M18 18h16M18 24h16M18 30h12" stroke="#fff" stroke-width="2.5"/></svg>Insurance</div>
  <div class="module" style="left:735px;top:434px"><svg viewBox="0 0 48 48" fill="none" stroke="#c8102e" stroke-width="3"><rect x="10" y="8" width="28" height="36" rx="2"/><rect x="18" y="4" width="12" height="6" fill="#c8102e"/><path d="M15 20l3 3 5-5M27 21h7M15 32l3 3 5-5M27 33h7"/></svg>Reports</div>

  <footer class="app-footer">© Copyright 2018. All Rights Reserved</footer>
</section>

<section class="screen app files-screen">
  <header class="app-header">
    <div class="logo"><span class="logo-name">Vantrel</span><span class="logo-tag">Professional Edition</span></div>
    <div class="phone"><svg width="18" height="18" viewBox="0 0 24 24"><circle cx="12" cy="12" r="10" fill="none" stroke="#c8102e" stroke-width="2"/><path d="M8 7l2 0 1 3-1.5 1a6 6 0 0 0 3.5 3.5l1-1.5 3 1v2a1 1 0 0 1-1 1A9 9 0 0 1 7 8a1 1 0 0 1 1-1z" fill="#c8102e"/></svg>(852) 3940 6127</div>
    <div class="lang">English ▾</div>
    <div class="user"><div class="avatar" role="img" aria-label="User avatar"></div>Ardenne ▾</div>
  </header>

  <h2 class="section-title">Others</h2>

  <div class="tile" style="left:59px;top:146px"><div class="thumb"><svg width="80" height="90" viewBox="0 0 80 90"><path d="M18 8h34l14 14v60H18z" fill="#fff"/><rect x="6" y="20" width="34" height="20" fill="#e53935"/><text x="23" y="35" fill="#fff" font-size="13" font-family="Roboto,sans-serif" text-anchor="middle">PDF</text><path d="M28 52h28M28 60h28M28 68h20" stroke="#ccc" stroke-width="3"/><circle cx="62" cy="78" r="10" fill="#e53935"/></svg></div><div class="tile-name">Medical Record Printing</div><div class="tile-meta">26/05/2018<span class="check"></span></div></div>
  <div class="tile" style="left:229px;top:146px"><div class="thumb scan" role="img" aria-label="Pulmonary CT scan image"></div><div class="tile-name">Pulmonary ct</div><div class="tile-meta">26/05/2018<span class="check"></span></div></div>
  <div class="tile" style="left:399px;top:146px"><div class="thumb scan" role="img" aria-label="Knee x-ray image"></div><div class="tile-name">Knee</div><div class="tile-meta">26/05/2018<span class="check"></span></div></div>
  <div class="tile" style="left:569px;top:146px"><div class="thumb scan" role="img" aria-label="Hand x-ray image"></div><div class="tile-name">x-ray hand</div><div class="tile-meta">26/05/2018<span class="check"></span></div></div>
  <div class="tile" style="left:739px;top:146px"><div class="thumb scan" role="img" aria-label="Frontal head x-ray image"></div><div class="tile-name">x-ray frontal</div><div class="tile-meta">26/05/2018<span class="check"></span></div></div>

  <div class="tile" style="left:59px;top:358px"><div class="thumb scan" role="img" aria-label="Chest x-ray image"></div><div class="tile-name">x-ray chest</div><div class="tile-meta">26/05/2018<span class="check"></span></div></div>
  <div class="tile" style="left:229px;top:358px"><div class="thumb ecg"><svg width="150" height="60" viewBox="0 0 150 60"><path d="M0 40h60l6-8 6 8 6-36 6 50 6-14h60" fill="none" stroke="#e05a8a" stroke-width="1.5"/></svg></div><div class="tile-name">ECG</div><div class="tile-meta">26/05/2018<span class="check"></span></div></div>
  <div class="tile" style="left:399px;top:358px"><div class="thumb"><svg width="90" height="90" viewBox="0 0 90 90"><circle cx="45" cy="45" r="42" fill="#e4e4e4"/><rect x="28" y="20" width="34" height="46" rx="2" fill="#fff" stroke="#555" stroke-width="2"/><rect x="38" y="16" width="14" height="7" fill="#c8102e"/><path d="M34 36h22M34 44h22M34 52h16" stroke="#888" stroke-width="2"/></svg></div><div class="tile-name">Patient report</div><div class="tile-meta">26/05/2018<span class="check"></span></div></div>
  <div class="tile" style="left:569px;top:358px"><div class="thumb"><svg width="80" height="90" viewBox="0 0 80 90"><path d="M18 8h34l14 14v60H18z" fill="#fff"/><rect x="6" y="20" width="34" height="20" fill="#e53935"/><text x="23" y="35" fill="#fff" font-size="13" font-family="Roboto,sans-serif" text-anchor="middle">PPT</text><path d="M28 52h28M28 60h28M28 68h20" stroke="#ccc" stroke-width="3"/><circle cx="62" cy="78" r="10" fill="#e53935"/></svg></div><div class="tile-name">Presentation</div><div class="tile-meta">26/05/2018<span class="check"></span></div></div>
  <div class="tile" style="left:739px;top:358px"><div class="thumb"><svg width="80" height="90" viewBox="0 0 80 90"><path d="M18 8h34l14 14v60H18z" fill="#fff"/><rect x="6" y="20" width="34" height="20" fill="#2e9e4f"/><text x="23" y="35" fill="#fff" font-size="13" font-family="Roboto,sans-serif" text-anchor="middle">XLS</text><path d="M28 52h28M28 60h28M28 68h20" stroke="#ccc" stroke-width="3"/><circle cx="62" cy="78" r="10" fill="#e53935"/></svg></div><div class="tile-name">Information shee</div><div class="tile-meta">26/05/2018<span class="check"></span></div></div>

  <div class="btn dark" style="left:60px;top:599px;width:116px">Previous page</div>
  <div class="btn blue" style="left:220px;top:599px;width:79px">Scan</div>
  <div class="btn blue" style="left:311px;top:599px;width:78px">Video</div>
  <div class="btn blue" style="left:401px;top:599px;width:79px">Import</div>
  <div class="btn blue" style="left:492px;top:599px;width:78px">Delete</div>
  <div class="btn blue" style="left:582px;top:599px;width:79px">Rename</div>
  <div class="btn blue" style="left:673px;top:599px;width:78px">Export</div>
  <div class="btn dark" style="left:793px;top:599px;width:102px">Next page</div>

  <div class="divider"></div>

  <div class="btn blue" style="left:59px;top:684px;width:116px">Compare</div>
  <div class="btn red" style="left:184px;top:684px;width:116px">Return</div>
  <div class="btn outline-blue" style="left:655px;top:684px;width:116px">Notify patient</div>
  <div class="btn outline-red" style="left:780px;top:684px;width:115px">Share report</div>

  <footer class="app-footer" style="height:59px">© Copyright 2018. All Rights Reserved</footer>
</section>

</body>
</html>
```